French Tech Blog : Wordpress theme

I need a wordpress theme made, for a french tech blog like gadgetpulse.com or lampcoins.com .. (the structure)

I will of course also need a logo that hold the identity of the website !

The blog's name is BlueMarmotte.com

The tone should be in the dark blue..

Target Market(s)

affiliate marketers, web entrepreneurs, 70% male between 20 and 35

Industry/Entity Type

Tech

```html
<!DOCTYPE html>
<html lang="en">
<head>
<meta charset="utf-8">
<title>Blue Marmotte – Tech Blog</title>
<link rel="stylesheet" href="https://fonts.googleapis.com/css2?family=PT+Sans:wght@400;700&display=swap">
<style>
:root{
  --navy:#0f2546;
  --deep:#0a2a52;
  --blue:#0d5aa0;
  --blue-bright:#1b73bd;
  --ink:#1d3d66;
  --text:#6b7a8c;
  --rule:#dde3ea;
  --white:#ffffff;
  --sky:#7fd0ef;
}
*{box-sizing:border-box;margin:0;padding:0}
html,body{width:880px;height:1200px;overflow:hidden}
body{
  font-family:"PT Sans",sans-serif;
  background:radial-gradient(ellipse at 50% 40%,#1a6fb3 0%,#0c3f78 55%,#06234a 100%);
  position:relative;
}
.page{position:absolute;left:56px;top:0;width:768px;height:1155px;background:var(--white)}
.abs{position:absolute}

/* header */
.brand{left:26px;top:44px;display:flex;align-items:center;gap:12px}
.brand-dot{width:40px;height:40px;border-radius:50%;background:var(--ink)}
.brand-name{font-size:35px;color:var(--ink);font-weight:400;letter-spacing:.5px}
.header-art{left:462px;top:0;width:274px;height:138px;
  background:linear-gradient(180deg,#1656a8 0%,#2a8fd3 55%,var(--sky) 100%);
  border-radius:40px 40px 0 0;opacity:.85}

/* nav */
.nav{left:0;top:138px;width:768px;height:38px;background:var(--navy)}
.nav-item{position:absolute;top:0;height:38px;line-height:38px;color:var(--white);font-size:11.5px;letter-spacing:.3px}
.nav-item.active{left:0;width:118px;text-align:center;background:linear-gradient(180deg,var(--blue-bright),#0b4d8c)}
.search{position:absolute;left:590px;top:8px;width:161px;height:23px;background:var(--white)}
.search svg{position:absolute;right:5px;top:4px}

/* main column */
.hero{left:11px;top:189px;width:488px;height:256px;
  background:radial-gradient(ellipse at 55% 35%,#bfe8ff 0%,#3a9fd6 25%,#0d5d93 60%,#062a4a 100%)}
.post{left:11px;width:488px;height:140px}
.post-title{position:absolute;left:0;top:0;font-size:16px;color:#1e2a36;font-weight:400;letter-spacing:.2px}
.post-thumb{position:absolute;left:0;top:30px;width:93px;height:72px;
  background:linear-gradient(135deg,#9fb3bf 0%,#3f7f93 50%,#1f5d72 100%)}
.post-text{position:absolute;left:99px;top:29px;width:390px;font-size:10.4px;line-height:14.4px;color:var(--text)}
.post-text p+p{margin-top:6.5px}
.read-more{position:absolute;left:99px;top:103px;width:55px;height:19px;border-radius:3px;
  background:linear-gradient(180deg,var(--blue-bright),#0a4a8a);color:var(--white);font-size:8.5px;font-weight:700;text-align:center;line-height:19px}
.share{position:absolute;left:380px;top:108px;width:100px;height:12px;border:1px solid #c9ced4;border-radius:2px;display:flex;align-items:center;gap:3px;padding:0 3px;font-size:7px;color:#333;letter-spacing:.5px}
.share .plus{width:8px;height:8px;background:#e0452b;border-radius:2px}
.share .sq{width:8px;height:8px;background:#3b8fd1}
.share .sq.b{background:#3b5998}.share .sq.c{background:#b03fae}
.share .lbl{width:44px}
.post-rule{position:absolute;left:0;top:138px;width:484px;height:1px;background:var(--rule)}
.col-rule{left:507px;top:182px;width:1px;height:958px;background:var(--rule)}

/* sidebar */
.social{left:528px;top:190px;display:flex;gap:5px}
.social span{width:26px;height:26px;border-radius:5px}
.callout{left:525px;width:216px;height:43px;border:1px solid var(--rule);display:flex;align-items:center;gap:8px;padding-left:10px;font-size:9.5px;font-weight:700;color:#222}
.callout i{width:22px;height:22px;border-radius:50%;display:block}
.widget-tabs{left:514px;top:347px;width:245px;height:185px;background:var(--blue);border:3px solid #0b4c88}
.tab{position:absolute;top:4px;font-size:11.5px;color:var(--white);height:19px;line-height:19px;white-space:nowrap}
.tab.on{left:6px;background:var(--white);color:#222;padding:0 6px}
.tab.archives{left:88px}
.tab.comments{left:160px}
.tab-body{position:absolute;left:6px;top:23px;width:230px;height:156px;background:var(--white);padding:14px 0 0 6px}
.list{list-style:none;font-size:10px;color:var(--text)}
.list li{display:flex;align-items:flex-start;gap:6px;line-height:14.4px}
.list li::before{content:"";flex:none;margin-top:4px;width:0;height:0;border-left:6px solid var(--ink);border-top:3px solid transparent;border-bottom:3px solid transparent}
.wide-head{left:514px;width:245px;height:29px;background:var(--blue);color:var(--white);font-size:12.5px;line-height:29px;padding-left:9px}
.featured{left:524px;top:598px;width:232px}
.featured .list{font-size:10.2px}
.featured .list li{margin-bottom:6px}
.fans-photo{left:544px;top:779px;width:187px;height:249px;border:1px solid #ccc;
  background:linear-gradient(180deg,#d9e1e6 0%,#b8a27a 45%,#6b6e70 75%,#4a4d52 100%)}
.badge{top:1049px;width:81px;height:81px}

/* footer */
.footer{left:58px;top:1170px;font-size:10.5px;color:#9fb8d3}
.footer b{color:var(--white);font-weight:400}
</style>
</head>
<body>
<div class="page">
  <div class="abs brand"><span class="brand-dot"></span><span class="brand-name">Blue Marmotte</span></div>
  <div class="abs header-art" role="img" aria-label="Silhouettes of a group of people standing together"></div>

  <nav class="abs nav">
    <span class="nav-item active">HOME</span>
    <span class="nav-item" style="left:154px">ABOUT US</span>
    <span class="nav-item" style="left:255px">TECH RESOURCES</span>
    <span class="nav-item" style="left:410px">CONTACT US</span>
    <div class="search"><svg width="14" height="14" viewBox="0 0 14 14"><circle cx="6" cy="6" r="4.2" fill="none" stroke="#1b73bd" stroke-width="2"/><line x1="9" y1="9" x2="13" y2="13" stroke="#1b73bd" stroke-width="2.4" stroke-linecap="round"/></svg></div>
  </nav>

  <div class="abs hero" role="img" aria-label="Finger touching a glowing blue touchscreen interface"></div>

  <article class="abs post" style="top:458px">
    <h2 class="post-title">The world of opportunities</h2>
    <div class="post-thumb" role="img" aria-label="Teal abstract digital numbers"></div>
    <div class="post-text"><p>Lorem ipsum dolor sit amet conse ctetuer adipiscing elit. Praeslum molestie lacu-sean nonummyendrerit mausellus porta. Fusce suscipit varius mium sociis natus.</p><p>Fuscefeu giat malesuada odiorbi nunc odio gravitcursus necuctus a loremecenas tristique orci ac sem. Duis ultricies pharetra magn accumsan malesuada orci.</p></div>
    <span class="read-more">Read More</span>
    <span class="share"><i class="plus"></i><span class="lbl">SHARE</span><i class="sq"></i><i class="sq b"></i><i class="sq c"></i></span>
    <span class="post-rule"></span>
  </article>
  <article class="abs post" style="top:615px">
    <h2 class="post-title">The world of opportunities</h2>
    <div class="post-thumb" role="img" aria-label="Teal abstract digital numbers"></div>
    <div class="post-text"><p>Lorem ipsum dolor sit amet conse ctetuer adipiscing elit. Praeslum molestie lacu-sean nonummyendrerit mausellus porta. Fusce suscipit varius mium sociis natus.</p><p>Fuscefeu giat malesuada odiorbi nunc odio gravitcursus necuctus a loremecenas tristique orci ac sem. Duis ultricies pharetra magn accumsan malesuada orci.</p></div>
    <span class="read-more">Read More</span>
    <span class="share"><i class="plus"></i><span class="lbl">SHARE</span><i class="sq"></i><i class="sq b"></i><i class="sq c"></i></span>
    <span class="post-rule"></span>
  </article>
  <article class="abs post" style="top:776px">
    <h2 class="post-title">The world of opportunities</h2>
    <div class="post-thumb" role="img" aria-label="Teal abstract digital numbers"></div>
    <div class="post-text"><p>Lorem ipsum dolor sit amet conse ctetuer adipiscing elit. Praeslum molestie lacu-sean nonummyendrerit mausellus porta. Fusce suscipit varius mium sociis natus.</p><p>Fuscefeu giat malesuada odiorbi nunc odio gravitcursus necuctus a loremecenas tristique orci ac sem. Duis ultricies pharetra magn accumsan malesuada orci.</p></div>
    <span class="read-more">Read More</span>
    <span class="share"><i class="plus"></i><span class="lbl">SHARE</span><i class="sq"></i><i class="sq b"></i><i class="sq c"></i></span>
    <span class="post-rule"></span>
  </article>
  <article class="abs post" style="top:935px">
    <h2 class="post-title">The world of opportunities</h2>
    <div class="post-thumb" role="img" aria-label="Teal abstract digital numbers"></div>
    <div class="post-text"><p>Lorem ipsum dolor sit amet conse ctetuer adipiscing elit. Praeslum molestie lacu-sean nonummyendrerit mausellus porta. Fusce suscipit varius mium sociis natus.</p><p>Fuscefeu giat malesuada odiorbi nunc odio gravitcursus necuctus a loremecenas tristique orci ac sem. Duis ultricies pharetra magn accumsan malesuada orci.</p></div>
    <span class="read-more">Read More</span>
    <span class="share"><i class="plus"></i><span class="lbl">SHARE</span><i class="sq"></i><i class="sq b"></i><i class="sq c"></i></span>
    <span class="post-rule"></span>
  </article>

  <span class="abs col-rule"></span>

  <div class="abs social">
    <span style="background:#5fc4ea"></span><span style="background:#3f4a55"></span><span style="background:#3b5998"></span><span style="background:#356aa0"></span><span style="background:#3aa845"></span><span style="background:#f2b21b;border-radius:50%"></span><span style="background:#3bb54a"></span>
  </div>
  <div class="abs callout" style="top:229px"><i style="background:#f08a24"></i>SUBSCRIBE TO OUR RSS FEED!</div>
  <div class="abs callout" style="top:280px"><i style="background:#4bb3e6"></i>FOLLOW US ON CHIRPER!</div>

  <div class="abs widget-tabs">
    <span class="tab on">Category</span>
    <span class="tab archives">Archives</span>
    <span class="tab comments">Comments</span>
    <div class="tab-body">
      <ul class="list">
        <li>Browsers</li><li>Computers</li><li>Featured</li><li>General</li><li>News</li><li>Parent Categor</li><li>Child Category</li><li>Tech</li><li>Lorem Ipsum is simply</li>
      </ul>
    </div>
  </div>

  <div class="abs wide-head" style="top:555px">Featured Posts</div>
  <div class="abs featured">
    <ul class="list">
      <li>Sample post with, links, paragraphs and com-ments..</li>
      <li>This is Just Going To Be Another Test Post..</li>
      <li>Keeping The Title Length Equal For Home..</li>
      <li>Another One to Fill Space..</li>
      <li>This Is Going To Be A Decent Length Title With Little Text..</li>
    </ul>
  </div>

  <div class="abs wide-head" style="top:744px">Blue Marmotte Friends &amp; Fans</div>
  <div class="abs fans-photo" role="img" aria-label="Group of friends posing in front of a clock tower"></div>
  <div class="abs badge" style="left:546px;background:linear-gradient(180deg,#e8f1f8 0%,#2a6fb8 100%)" role="img" aria-label="Partner badge"></div>
  <div class="abs badge" style="left:646px;background:#1e1a1c" role="img" aria-label="Partner badge"></div>
</div>
<div class="abs footer">Copyright © <b>Blue Marmotte</b></div>
</body>
</html>
```